Concise,Good colour matching,Good looks design for "HERD SCAN QUICK ASSAY FOR LIVESTOCK"

Product Positioning: Affordable test for Large Animals (Livestock/Veterinary Use)
Product Name: HERD SCAN Quick Assay Kit (for large animals, e.g., cattle, horses, swine,Avian,sheep).

2. Packaging Requirements

A. Visual Design
Color Scheme:
Green/Blue/Orange/Yellow/Red/Gray/White(chose 2~4 colors)

Mandatory Info:
Brand logo ("HERD SCAN")

Target Market(s)

Southeast Asia, Africa, Middle East, South America

Industry/Entity Type

Veterinary diagnostic for LIVESTOCK

Colors

Designer to choose colors to be used in the design.

Requirements
Nice to have
• Concise,Good colour matching,Good looks

```html
<!DOCTYPE html>
<html lang="en">
<head>
<meta charset="utf-8">
<title>HERD SCAN Quick Assay Kit – Carton Dieline</title>
<link href="https://fonts.googleapis.com/css2?family=Roboto:wght@500;700;900&family=Poppins:wght@300;400;600;700&display=swap" rel="stylesheet">
<style>
  :root{
    --navy:#1c3a6e;
    --sky:#6fcde3;
    --orange:#f29a2e;
    --white:#ffffff;
    --cut:#d6245e;
    --fold:#5fb6dc;
  }
  *{box-sizing:border-box;margin:0;padding:0}
  html,body{width:1035px;height:1200px;overflow:hidden;background:var(--white)}
  .canvas{position:relative;width:1035px;height:1200px}
  .dieline{position:absolute;inset:0}
  .panel{position:absolute;overflow:hidden}
  .panel svg.deco{position:absolute;inset:0}

  .brand{font-family:"Roboto",sans-serif;font-weight:900;letter-spacing:-1px;white-space:nowrap;line-height:1}
  .brand sup{font-size:.3em;font-weight:700;vertical-align:top;position:relative;top:.1em;margin-left:2px;letter-spacing:0}
  .tagline{font-family:"Roboto",sans-serif;font-weight:500;letter-spacing:2.6px;text-align:center;font-size:19.5px;line-height:24px}
  .maker{position:absolute;left:293px;text-align:left;font-family:"Poppins",sans-serif;white-space:nowrap}
  .maker .by{font-weight:400;font-size:11.5px;line-height:13px;display:block}
  .maker .name{font-weight:700;font-size:18px;line-height:20px;letter-spacing:.3px;display:block}

  /* top tuck panel */
  .panel-top{left:309px;top:90px;width:419px;height:307px;background:var(--white)}
  .panel-top .brand{position:absolute;top:35px;left:0;width:100%;text-align:center;font-size:51px;color:var(--navy)}
  .panel-top .tagline{position:absolute;top:95px;left:0;width:100%}
  .panel-top .tagline .l1{color:var(--navy);display:block}
  .panel-top .tagline .l2{color:var(--sky);display:block}
  .rule{position:absolute;top:151px;left:64px;width:291px;height:1.5px;background:var(--navy)}
  .species{position:absolute;top:167px;left:54px;display:flex;gap:10.5px}
  .species span{width:43px;height:43px;border-radius:50%;border:2.5px solid var(--sky);background:radial-gradient(circle,var(--navy) 0 38%,var(--white) 40%)}
  .tag{position:absolute;left:19px;top:220px;width:64px;height:66px;background:var(--navy);border-radius:6px 6px 0 0;color:var(--white);font-family:"Roboto",sans-serif;font-weight:700;font-size:14.5px;line-height:17.5px;letter-spacing:.6px;text-align:center;padding-top:6px}
  .panel-top .maker{top:264px;color:var(--white)}

  /* front & bottom panels */
  .panel-face{left:309px;width:419px;height:223px;background:var(--navy)}
  .panel-front{top:397px}
  .panel-bottom{top:928px;height:222px;transform:rotate(180deg)}
  .panel-face .brand{position:absolute;top:24px;left:0;width:100%;text-align:center;font-size:51px;color:var(--white)}
  .panel-face .tagline{position:absolute;top:88px;left:0;width:100%;color:var(--white)}
  .panel-face .tagline span{display:block}
  .rapid{position:absolute;left:23px;top:144px;display:flex;align-items:center;gap:6px}
  .timer{width:36px;height:36px;border-radius:50%;background:var(--orange);display:flex;align-items:center;justify-content:center}
  .timer i{width:28px;height:28px;border-radius:50%;border:1.5px dashed var(--white);color:var(--white);font-style:normal;font-family:"Roboto",sans-serif;font-weight:700;font-size:8.5px;line-height:9px;text-align:center;display:flex;flex-direction:column;justify-content:center}
  .timer i b{font-size:10px}
  .rapid p{color:var(--white);font-family:"Roboto",sans-serif;font-weight:700;font-size:10px;line-height:14px}
  .panel-face .maker{top:176px;color:var(--navy)}

  /* back */
  .panel-back{left:309px;top:620px;width:419px;height:308px;background:var(--navy)}

  /* side panels */
  .panel-side{top:620px;width:224px;height:308px;background:var(--navy)}
  .panel-left{left:85px}
  .panel-right{left:728px}
  .side-inner{position:absolute;left:-42px;top:42px;width:308px;height:224px;color:var(--white)}
  .panel-left .side-inner{transform:rotate(-90deg)}
  .panel-right .side-inner{transform:rotate(90deg)}
  .side-inner .brand{position:absolute;font-size:35px;letter-spacing:-.5px}
  .panel-left .brand{top:25px;left:49px}
  .info{position:absolute;left:41px;font-family:"Poppins",sans-serif;font-weight:400;font-size:11.2px;line-height:14px;white-space:nowrap}
  .info.i1{top:73px}.info.i2{top:94px}.info.i3{top:116px}
  .marks{position:absolute;left:96px;top:199px;display:flex;gap:8px;align-items:center}
  .marks span{width:13px;height:13px;background:var(--sky);opacity:.9}
  .marks span.round{border-radius:50%}
  .panel-right .brand{top:9px;left:21px}
  .subtitle{position:absolute;top:47px;left:21px;font-family:"Roboto",sans-serif;font-weight:500;font-size:17px;letter-spacing:2px;color:var(--sky);line-height:20px}
  .features{position:absolute;top:72px;left:21px;font-family:"Poppins",sans-serif;font-size:10.6px;line-height:13.4px;white-space:nowrap}
  .features h3{font-weight:700;font-size:10.6px}
  .features p{font-weight:300;margin-bottom:6.6px}
</style>
</head>
<body>
<div class="canvas">

  <svg class="dieline" width="1035" height="1200" viewBox="0 0 1035 1200">
    <path d="M309 90 V60 Q309 49 330 49 H707 Q728 49 728 70 V90" fill="var(--white)"/>
    <path fill="none" stroke="var(--cut)" stroke-width="1.6" stroke-linejoin="round"
      d="M309 90 Q309 49 350 49 H687 Q728 49 728 90 V397 L812 404 V613 L728 620 H952 L958 627 L1008 632 V911 L958 922 L952 928 H728 L812 935 V1143 L728 1150 H534 Q534 1130 518 1130 Q502 1130 502 1150 H309 L224 1143 V935 L309 928 H85 L77 922 L28 911 V632 L77 627 L85 620 H309 L224 613 V404 L309 397 Z"/>
  </svg>

  <section class="panel panel-top">
    <svg class="deco" width="419" height="307" viewBox="0 0 419 307">
      <path d="M0 282 H240 Q252 282 260 273 L276 254 Q283 246 295 246 H419 V307 H0 Z" fill="var(--navy)"/>
      <path d="M0 275 H230 Q240 275 248 266 L264 247 Q271 239 283 239 H419" fill="none" stroke="var(--sky)" stroke-width="5"/>
    </svg>
    <h1 class="brand">HERD SCAN<sup>TM</sup></h1>
    <p class="tagline"><span class="l1">AFFORDABLE DIAGNOSTICS</span><span class="l2">FOR HEALTHY HERDS</span></p>
    <div class="rule"></div>
    <div class="species">
      <span role="img" aria-label="Cattle silhouette icon"></span>
      <span role="img" aria-label="Horse silhouette icon"></span>
      <span role="img" aria-label="Sheep silhouette icon"></span>
      <span role="img" aria-label="Chicken silhouette icon"></span>
      <span role="img" aria-label="Pig silhouette icon"></span>
      <span role="img" aria-label="Goat silhouette icon"></span>
    </div>
    <div class="tag">LARGE<br>ANIMAL</div>
    <p class="maker"><span class="by">Manufactured by</span><span class="name">AGROVANTA</span></p>
  </section>

  <section class="panel panel-face panel-front">
    <svg class="deco" width="419" height="223" viewBox="0 0 419 223">
      <path d="M0 207 H234 Q246 207 254 198 L268 179 Q275 170 287 170 H419 V223 H0 Z" fill="var(--white)"/>
      <path d="M0 192 H228 Q238 192 246 183 L262 164 Q269 156 281 156 H419" fill="none" stroke="var(--sky)" stroke-width="5"/>
    </svg>
    <h2 class="brand">HERD SCAN<sup>TM</sup></h2>
    <p class="tagline"><span>AFFORDABLE DIAGNOSTICS</span><span>FOR HEALTHY HERDS</span></p>
    <div class="rapid"><div class="timer"><i><b>10</b>MIN</i></div><p>RAPID RESULTS<br>&nbsp;IN 10 MINUTES</p></div>
    <p class="maker"><span class="by">Manufactured by</span><span class="name">AGROVANTA</span></p>
  </section>

  <section class="panel panel-back"></section>

  <section class="panel panel-side panel-left">
    <div class="side-inner">
      <h2 class="brand">HERD SCAN<sup>TM</sup></h2>
      <p class="info i1">Manufactured by AGROVANTA</p>
      <p class="info i2">Storage: 2~30°C,Do not freeze</p>
      <p class="info i3">See the instructions for other contents</p>
      <div class="marks">
        <span class="round"></span><span></span><span></span><span class="round"></span><span></span><span class="round"></span>
      </div>
    </div>
  </section>

  <section class="panel panel-side panel-right">
    <div class="side-inner">
      <h2 class="brand">HERD SCAN<sup>TM</sup></h2>
      <p class="subtitle">QUICK ASSAY</p>
      <div class="features">
        <h3>FAST &amp; EFFICIENT:</h3>
        <p>Rapid test results in less than 10 minutes from<br>prep to completion</p>
        <h3>AFFORDABLE:</h3>
        <p>Colloidal gold-based rapid tests that combine<br>high accuracy with cost-effectiveness.</p>
        <h3>RELIABLE &amp; SIMPLE:</h3>
        <p>Stable test performance with 2~30°C,Easy to<br>operate,no professional skills required.</p>
      </div>
    </div>
  </section>

  <section class="panel panel-face panel-bottom">
    <svg class="deco" width="419" height="222" viewBox="0 0 419 222">
      <path d="M0 207 H234 Q246 207 254 198 L268 179 Q275 170 287 170 H419 V222 H0 Z" fill="var(--white)"/>
      <path d="M0 192 H228 Q238 192 246 183 L262 164 Q269 156 281 156 H419" fill="none" stroke="var(--sky)" stroke-width="5"/>
    </svg>
    <h2 class="brand">HERD SCAN<sup>TM</sup></h2>
    <p class="tagline"><span>AFFORDABLE DIAGNOSTICS</span><span>FOR HEALTHY HERDS</span></p>
    <div class="rapid"><div class="timer"><i><b>10</b>MIN</i></div><p>RAPID RESULTS<br>&nbsp;IN 10 MINUTES</p></div>
    <p class="maker"><span class="by">Manufactured by</span><span class="name">AGROVANTA</span></p>
  </section>

  <svg class="dieline" width="1035" height="1200" viewBox="0 0 1035 1200" style="pointer-events:none">
    <g stroke="var(--fold)" stroke-width="0.8" fill="none">
      <line x1="309" y1="90" x2="728" y2="90"/>
      <line x1="309" y1="397" x2="728" y2="397"/>
      <line x1="309" y1="620" x2="728" y2="620"/>
      <line x1="309" y1="928" x2="728" y2="928"/>
      <line x1="309" y1="397" x2="309" y2="1150"/>
      <line x1="728" y1="397" x2="728" y2="1150"/>
      <line x1="952" y1="620" x2="952" y2="928"/>
      <line x1="85" y1="620" x2="85" y2="928"/>
    </g>
    <path d="M1008 632 V911 M28 632 V911" stroke="var(--cut)" stroke-width="1.6"/>
  </svg>

</div>
</body>
</html>
```